KBT Business Cards

We require business cards for our business. We would like a matte black back to the card, with our logo centred in the middle. The front side of the card is open to design.

Target Market(s)

Clients looking for legal services (professional)

Industry/Entity Type

Legal

Contact Information for Business Card

Doran Kelbrath
Partner
Mobile: 0461 738 524
Email: doran@kbtlaw.co
Website: www.kbtlaw.co
Level 3, 118 Wendmore Street
Sydney NSW 2000

Font styles to use
Other font styles liked:
• Avenir

Colors
f04a50
ffffff
1b1b1b

Requirements
Must have
• Black back with logo included in the centre of the card.
• Our font is Avenir.

```html
<!DOCTYPE html>
<html lang="en">
<head>
<meta charset="utf-8">
<title>Kelbrath Bane Legal – Business Cards</title>
<link rel="stylesheet" href="https://fonts.googleapis.com/css2?family=Nunito+Sans:wght@400;600;800&display=swap">
<style>
  :root {
    --backdrop: #2b2b2d;
    --card: #1b1b1b;
    --accent: #f04a50;
    --accent-deep: #d4204a;
    --white: #ffffff;
    --muted: #e6e6e6;
  }
  * { margin: 0; padding: 0; box-sizing: border-box; }
  html, body {
    width: 1200px; height: 779px; overflow: hidden;
    background: var(--backdrop);
    font-family: "Nunito Sans", "Avenir", sans-serif;
  }
  .stage { position: relative; width: 1200px; height: 779px; }
  .card {
    position: absolute;
    width: 540px; height: 310px;
    background: var(--card);
    border-bottom: 3px solid var(--accent-deep);
    border-left: 2px solid var(--accent-deep);
    box-shadow: 0 18px 40px rgba(0,0,0,.45);
  }
  .card--back { left: 70px; top: 70px; }
  .card--front { left: 590px; top: 400px; }

  .brand-mark {
    display: flex; align-items: center; gap: 14px;
    color: var(--white);
  }
  .brand-mark__square {
    width: 34px; height: 34px; background: var(--accent-deep);
  }
  .card--back .brand-mark {
    position: absolute; left: 50%; top: 50%;
    transform: translate(-50%, -50%);
  }
  .card--back .brand-mark__square { background: #6f6f72; }
  .card--back .brand-name { color: #8a8a8d; }
  .brand-name {
    font-weight: 800; font-size: 19px; line-height: 1.02;
    text-transform: uppercase; letter-spacing: .3px;
  }

  .card--front .brand-mark { position: absolute; left: 54px; top: 116px; }
  .divider {
    position: absolute; left: 262px; top: 52px;
    width: 2px; height: 200px;
    background: linear-gradient(to bottom, transparent, var(--white) 20%, var(--white) 80%, transparent);
  }
  .contact { position: absolute; left: 286px; top: 70px; color: var(--white); }
  .contact__name { color: var(--accent-deep); font-weight: 800; font-size: 19px; line-height: 1.1; }
  .contact__role { font-size: 14px; margin-bottom: 14px; }
  .contact__address { font-size: 13.5px; line-height: 1.35; margin-bottom: 12px; }
  .contact__list { list-style: none; font-size: 13.5px; line-height: 1.5; }
  .contact__list li { display: flex; align-items: center; gap: 10px; }
  .contact__icon { width: 14px; height: 14px; flex: none; }
</style>
</head>
<body>
<main class="stage">
  <section class="card card--back" aria-label="Card back">
    <div class="brand-mark">
      <span class="brand-mark__square"></span>
      <span class="brand-name">Kelbrath<br>Bane<br>Legal</span>
    </div>
  </section>

  <section class="card card--front" aria-label="Card front">
    <div class="brand-mark">
      <span class="brand-mark__square"></span>
      <span class="brand-name">Kelbrath<br>Bane<br>Legal</span>
    </div>
    <div class="divider"></div>
    <div class="contact">
      <p class="contact__name">Doran Kelbrath</p>
      <p class="contact__role">Partner</p>
      <p class="contact__address">Level 3, 118 Wendmore Street<br>Sydney NSW 2000</p>
      <ul class="contact__list">
        <li>
          <svg class="contact__icon" viewBox="0 0 14 14" aria-hidden="true"><rect x="3" y="1" width="8" height="12" rx="1.5" fill="none" stroke="#d4204a" stroke-width="1.6"/><circle cx="7" cy="10.5" r=".9" fill="#d4204a"/></svg>
          0461 738 524
        </li>
        <li>
          <svg class="contact__icon" viewBox="0 0 14 14" aria-hidden="true"><rect x="1" y="3" width="12" height="8" fill="#d4204a"/><path d="M1 3 L7 8 L13 3" fill="none" stroke="#1b1b1b" stroke-width="1.2"/></svg>
          doran@kbtlaw.co
        </li>
        <li>
          <svg class="contact__icon" viewBox="0 0 14 14" aria-hidden="true"><circle cx="7" cy="7" r="6" fill="#d4204a"/><path d="M1 7 H13 M7 1 C4 4 4 10 7 13 M7 1 C10 4 10 10 7 13" fill="none" stroke="#1b1b1b" stroke-width="1"/></svg>
          www.kbtlaw.co
        </li>
      </ul>
    </div>
  </section>
</main>
</body>
</html>
```